Pagina Lartovira

The Lartovira is a company dealing with leasing and selling real estate. The current site can be accessed at www.lartovira-exemplo.com.br. We intend to redesign the look of the site and for that we would like to redesign the home page and the page with information and pictures of the property. The homepage should maintain the characteristics of the current common design simple, short and straightforward. The page with the data of the properties should be accessed with two changes page as it is currently running. The search from the map by region and should be maintained.
The page containing the information of the property will provide a total of 15 small pictures that when clicked will appear in larger size. The colors to be used should be orange, blue, black and white. The map can be maintained in the current colors.
Updates

Payment guaranteed. Deadline for submission of designs April 27.

Industry/Entity Type

Real Estate

Requirements
Must have
• Search by map regions and search box
address
keep colors from the current page
phones
clean look
Nice to have
• clean look
Should not have
• We like the current page. We just want to make it compatible with modern and new design trends and monitors.

```html
<!DOCTYPE html>
<html lang="en">
<head>
<meta charset="utf-8">
<title>Lartovira</title>
<link href="https://fonts.googleapis.com/css2?family=Nunito+Sans:wght@400;600&family=Oswald:wght@400&display=swap" rel="stylesheet">
<style>
:root{
  --navy:#3b3f72;
  --navy-band:rgba(62,66,118,.88);
  --orange:#f0743a;
  --orange-dark:#c9521f;
  --white:#ffffff;
  --panel:rgba(255,255,255,.86);
  --text:#4d4f63;
  --sky:#8fc0ea;
}
*{margin:0;padding:0;box-sizing:border-box}
html,body{width:1200px;height:735px;overflow:hidden}
body{font-family:"Nunito Sans",sans-serif;color:var(--text);position:relative;background:#ffffff}
.hero-photo{position:absolute;inset:0;
  background:linear-gradient(180deg,#9ecbf0 0%,#b7d8f2 14%,#d8b57d 32%,#c98e52 48%,#8c6a3c 60%,#5f7c3c 78%,#6f9a45 88%,#4d5a3a 100%)}
.topbar{position:absolute;top:11px;left:772px;font-size:10.5px;color:var(--navy);letter-spacing:.2px;display:flex;align-items:center;gap:8px}
.topbar .sep{opacity:.6}
.topbar .social{display:flex;gap:5px;margin-left:2px}
.topbar .social span{width:15px;height:15px;border-radius:50%;background:var(--navy);display:block}
.callus{position:absolute;top:36px;left:810px;font-size:15px;line-height:15px;color:var(--navy);text-transform:uppercase}
.callus-divider{position:absolute;top:36px;left:871px;width:1px;height:31px;background:rgba(59,63,114,.4)}
.phones{position:absolute;top:34px;left:884px;font-size:13.5px;line-height:17.5px;color:var(--navy)}
.navband{position:absolute;top:82px;left:0;width:1200px;height:38px;background:var(--navy-band)}
.logo-box{position:absolute;top:57px;left:183px;width:159px;height:81px;background:#f3f3f4;display:flex;align-items:center;justify-content:center;gap:6px;box-shadow:0 2px 4px rgba(0,0,0,.2)}
.logo-box .mark{width:10px;height:10px;background:var(--navy)}
.logo-box .name{font-size:20px;font-weight:600;color:var(--navy)}
.nav{position:absolute;top:82px;left:383px;display:flex;height:38px;font-size:10.5px;text-transform:uppercase;color:var(--white)}
.nav a{color:var(--white);text-decoration:none;padding:0 7px;line-height:38px}
.nav a.active{background:var(--orange);padding:0 8px}
.headline{position:absolute;top:160px;left:688px;color:var(--white);text-transform:uppercase;text-shadow:0 1px 3px rgba(0,0,0,.25)}
.headline .small{font-size:16px;color:var(--navy);text-shadow:none;display:block;line-height:18px}
.headline .big{font-size:33px;line-height:32px}
.headline .from{font-size:16px}
.welcome-panel{position:absolute;top:497px;left:0;width:1200px;height:102px;background:var(--panel)}
.map-card{position:absolute;top:359px;left:193px;width:138px;height:208px;background:var(--white);padding:3px;box-shadow:0 2px 6px rgba(0,0,0,.25)}
.map-card .map{width:100%;height:100%;background:linear-gradient(135deg,#6fb0e0,#a9d3ee 45%,#f2e3b0 60%,#8cc3e8)}
.ribbon{position:absolute;top:534px;left:184px;width:156px;height:31px;background:var(--orange);color:var(--white);font-family:"Oswald",sans-serif;font-size:13.5px;text-transform:uppercase;line-height:31px;text-align:center;letter-spacing:-.2px}
.ribbon-fold{position:absolute;top:565px}
.welcome-divider{position:absolute;top:508px;left:360px;width:1px;height:80px;background:rgba(59,63,114,.3)}
.welcome{position:absolute;top:514px;left:381px;width:632px}
.welcome h1{font-weight:400;font-size:17.5px;color:var(--navy);text-transform:uppercase;letter-spacing:.3px;margin-bottom:2px}
.welcome p{font-size:10.3px;line-height:14.5px}
.searchbar{position:absolute;top:599px;left:0;width:1200px;height:32px;background:var(--navy-band);color:var(--white);font-size:12px;text-transform:uppercase}
.searchbar .label{position:absolute;left:185px;top:9px}
.searchbar .divider{position:absolute;left:360px;top:6px;width:1px;height:20px;background:rgba(255,255,255,.4)}
.radio{position:absolute;top:9px;display:flex;align-items:center;gap:6px}
.radio i{width:10px;height:10px;border-radius:50%;background:#e8e8ee;display:block;position:relative}
.radio i.on::after{content:"";position:absolute;left:3px;top:3px;width:4px;height:4px;border-radius:50%;background:#3f7fc9}
.select{position:absolute;left:548px;top:7px;width:188px;height:18px;background:#f2f2f4;border:1px solid #c9c9d2;color:#8a8a96;font-size:11px;text-transform:none;padding-left:8px;line-height:16px}
.select svg{position:absolute;right:6px;top:6px}
.btn-search{position:absolute;left:746px;top:7px;width:53px;height:18px;background:var(--orange);color:var(--white);font-size:11px;text-transform:none;text-align:center;line-height:18px}
.address{position:absolute;top:689px;left:0;width:1200px;height:21px;background:rgba(240,116,58,.92);color:var(--white);font-size:10.5px;line-height:21px;padding-left:382px}
.footer{position:absolute;top:710px;left:0;width:1200px;height:25px;background:#3e4276;color:var(--white);font-size:9.5px;line-height:25px}
.footer .links{position:absolute;left:184px}
.footer .links span{opacity:.5;margin:0 4px}
.footer .copy{position:absolute;right:185px}
</style>
</head>
<body>
<div class="hero-photo" role="img" aria-label="Photo of a large Mediterranean-style house with palm trees, flowers and a lawn under a blue sky"></div>

<div class="topbar">
  <span>CONTACT US</span><span class="sep">|</span><span>RESTRICTED AREA</span><span class="sep">|</span>
  <span class="social"><span></span><span></span><span></span></span>
</div>
<div class="callus">Call us<br>today</div>
<div class="callus-divider"></div>
<div class="phones">Lease (48) 3100-4521<br>Sales: (48) 8877-2603</div>

<div class="navband"></div>
<div class="logo-box"><span class="mark"></span><span class="name">Lartovira</span></div>
<nav class="nav">
  <a class="active">The Company</a><a>Location</a><a>List your property</a><a>Owner info</a><a>Information for tenant</a><a>Request your property</a>
</nav>

<div class="headline">
  <span class="small">In business of</span>
  <span class="big">Real Estate</span> <span class="from">from</span><br>
  <span class="big">Fifteen Years</span>
</div>

<div class="welcome-panel"></div>
<div class="map-card"><div class="map" role="img" aria-label="Regional map of the island and coastline"></div></div>
<div class="ribbon">Search property by region</div>
<svg class="ribbon-fold" style="left:184px" width="8" height="6"><polygon points="0,0 8,0 8,6" fill="var(--orange-dark)"/></svg>
<svg class="ribbon-fold" style="left:332px" width="8" height="6"><polygon points="0,0 8,0 0,6" fill="var(--orange-dark)"/></svg>
<div class="welcome-divider"></div>
<div class="welcome">
  <h1>Welcome to Lartovira</h1>
  <p>Lorem ipsum dolor sit amet, consectetur adipiscing elit. Nunc egestas consectetur gravida. Sed tincidunt accumsan sem sit amet aliquet. Etiam iaculis consectetur porta. Vestibulum mollis luctus pulvinar. Proin purus ligula, dictum vestibulum fringilla ut, pharetra ut risus. Lorem ipsum dolor sit amet, consectetur adipiscing elit. Sed quis vehicula elit.</p>
</div>

<div class="searchbar">
  <span class="label">Search for properties:</span>
  <span class="divider"></span>
  <span class="radio" style="left:383px"><i class="on"></i>To buy</span>
  <span class="radio" style="left:469px"><i></i>Rent</span>
  <div class="select">Every<svg width="7" height="4"><polygon points="0,0 7,0 3.5,4" fill="#9a9aa6"/></svg></div>
  <div class="btn-search">Search</div>
</div>

<div class="address">Rua Alvaro Mendes, 48 - Street Corner with Paulo Ramires - Centro Vila Serena -</div>
<footer class="footer">
  <div class="links">Home<span>|</span>Company<span>|</span>Privacy Policy<span>|</span>Terms &amp; Conditions</div>
  <div class="copy">(C) 2013 - Lartovira - All rights reserved.</div>
</footer>
</body>
</html>
```